Snoutsaver.net Dog Coupon Site Website Design

TailThrift - Dog Coupon Site Design Brief

Project Overview
**Site Name:** SnoutSaver.net
**Purpose:** A modern coupon aggregation platform specifically for dog and pet-related products and services
**Target Audience:** Dog owners, pet enthusiasts, budget-conscious pet parents

Brand Identity & Visual Direction

Typography
- **Headers:** Modern sans-serif (Inter or similar) - Clean and friendly
- **Body:** Readable sans-serif with good mobile legibility
- **Accent:** Playful but professional font for coupon codes

Design Principles
- **Flat Design:** Clean, minimal with subtle shadows
- **Friendly & Approachable:** Rounded corners, soft edges
- **Trust-Building:** Clear pricing, transparent savings
- **Scannable:** Easy-to-read coupon codes and offers

## User Experience & Functionality

### Homepage Features
1. **Hero Section**
- Clear value proposition
- Search functionality
- Featured savings highlight

2. **Coupon Cards**
- One-click copy functionality
- Clear discount display
- Store/brand logos
- Expiration dates
- "Get Deal" call-to-action

3. **Navigation**
- Categories (Food, Toys, Health, Services, etc.)
- Popular stores
- Latest deals

### Interactive Elements
- **Copy Button:** Instant feedback when coupon copied
- **Deal Pages:** Detailed offer information, terms, store details
- **Search & Filter:** By category, store, discount amount
- **Mobile Menu:** Hamburger navigation for mobile

## Technical Requirements

### Responsive Design
- **Mobile-First:** Optimized for touch interactions
- **Tablet:** Adapted layout for medium screens
- **Desktop:** Full-width utilization with sidebar potential

### Performance
- **Fast Loading:** Optimized images, minimal JavaScript
- **Accessibility:** WCAG compliant, screen reader friendly
- **SEO Optimized:** Structured data for deals and offers

## Content Strategy

### Deal Categories
- Dog Food & Treats
- Toys & Accessories
- Health & Grooming
- Training & Services
- Outdoor & Travel

### Key Messaging
- "Save on everything your dog loves"
- "Verified deals updated daily"
- "Your pup deserves the best for less"

## Conversion Optimization

### Trust Elements
- Deal verification badges
- User reviews/ratings
- Clear savings calculations
- Expiration date transparency

### Call-to-Actions
- "Copy Code" (primary action)
- "Get Deal" (secondary action)
- "View All [Store] Deals"

## Success Metrics
- Coupon copy rate
- Click-through to retailer
- User return visits
- Mobile vs desktop usage
- Category performance

This design brief ensures a user-friendly, trustworthy platform that makes finding and using pet deals effortless while maintaining a warm, dog-loving community feel.

1. Design Objective
Create a warm, energetic space where dog lovers instantly feel welcomed and confident they’re finding genuine savings for their furry friends. Everything from the layout to the smallest icon should reinforce trust, delight, and simplicity.
2. Visual Personality
Color Palette: Soft, cheerful hues—think warm yellows and gentle blues—that evoke sunshine and playfulness without overwhelming.
Typography:
Headings: A modern, friendly sans‑serif (like Inter) with open letterforms to feel approachable.
Body Copy: Highly legible sans‑serif with generous line spacing for comfort on small screens.
Accent Font: A slightly quirky, hand‑drawn style used sparingly for coupon codes and special call‑outs, giving a personal, “paw‑picked” touch.
Imagery & Icons: Real‑life photographs of happy dogs interspersed with clean line‑icons of bones, paw prints, and hearts. Rounded shapes and subtle shadows keep the look soft and contemporary.
3. Layout & Hierarchy
Hero Area:
Full‑bleed image of a joyful dog, overlaid with a single, punchy tagline (“Save on everything your dog loves”).
Prominent search bar centered to invite exploration.
Offer Grid:
Generous white space around each coupon card so the eye can rest and scan easily.
Coupon cards feature a bold discount label, brand logo, and a friendly “Get Deal” button.
A playful “Copied!” animation briefly replaces the button once the code is grabbed.
Navigation:
A fixed header with clear category labels (Food, Toys, Health, Services).
A secondary “Popular Stores” carousel below to spotlight key partners.
4. Interaction & Motion
Micro‑interactions:
Hover state for cards subtly lifts the card and deepens its shadow, inviting a click.
Copy‑code button pulses once on hover, hinting at its one‑click magic.
Transitions:
Smooth fades between deal filters and search results to reassure users that the site is responding.
Loading indicators shaped like spinning collars or wagging tails to keep the theme consistent.
5. Accessibility & Inclusivity
Ensure all text meets contrast standards so every pet parent—regardless of vision—can read offers with ease.
Interactive elements sized for easy tapping on touchscreens.
Alt‑text for all imagery describing dogs, products, and actions for screen‑reader users.
6. Emotional Tone
From the moment someone lands on SnoutSaver.net, they should feel the joy of treating their dog without guilt. Friendly copy (“Your pup deserves the best for less”) paired with bright visuals will create a sense of community and shared passion.
7. Success by Design
Scan‑ability: Users should spot great deals in under two seconds.
Trust Signals: Badges (“Verified Savings”), clear expiration dates, and reviewer star icons should feel earned and prominent.
Return Visits: A “My Favorite Deals” heart icon encourages saving and returning, reinforced by subtle reminders in the UI.
This design approach keeps dog lovers front and center—making sure every graphic, font choice, and interaction feels like it was lovingly tailored for them.

Target Market(s)

Dog Lovers looking for good deals

Industry/Entity Type

Coupon Code

Number of Pages Required

4 page

Font styles to use
Sans Serif

Requirements
Must have
• Modern look, coupon copy cards it's a deal site and I want the coupon code and copy in the coupon card, blog section, review section, modern footer/header
Nice to have
• Modern coupon code website, easy to use

```html
<!DOCTYPE html>
<html lang="en">
<head>
<meta charset="utf-8">
<title>SnoutSaver.net – Dog Deals &amp; Coupons</title>
<link rel="stylesheet" href="https://fonts.googleapis.com/css2?family=Lexend:wght@300;400;500;600&display=swap">
<style>
:root{
  --ink:#1d1d1f;
  --muted:#3a3a3a;
  --blue:#8ed3ee;
  --blue-deep:#4aa9d3;
  --blue-soft:#eef8fc;
  --yellow:#f0bf4c;
  --yellow-soft:#fbf6ea;
  --grey-bg:#f6f6f6;
  --line:#d9d9d9;
  --green:#41b648;
  --coral:#ef6d4a;
  --red:#e24a5a;
  --teal:#2fa7a0;
  --purple:#8c63c4;
  --pink:#f07a8f;
}
*{box-sizing:border-box;margin:0;padding:0}
html,body{width:1200px;height:3487px;overflow:hidden}
body{position:relative;background:#fff;font-family:"Lexend",sans-serif;color:var(--ink);font-weight:300}
.abs{position:absolute}
.band{position:absolute;left:0;width:1200px;background:var(--grey-bg)}
.ph{position:absolute}

/* header */
.brand{position:absolute;display:flex;align-items:center;justify-content:center;border-radius:50%;background:var(--blue);color:#fff;font-weight:600;letter-spacing:.5px}
.nav{position:absolute;top:44px;font-size:13px;font-weight:400;text-transform:uppercase}
.nav.active{color:var(--blue-deep)}
.round-btn{position:absolute;border-radius:50%;border:1.5px solid var(--blue);display:flex;align-items:center;justify-content:center;background:#fff}

/* hero */
.hero-title{left:112px;top:206px;font-size:32px;font-weight:500;line-height:52px}
.hero-title em{font-style:normal;color:var(--yellow)}
.hero-sub{left:112px;top:330px;width:430px;font-size:16px;line-height:36px;color:var(--muted)}
.search{left:112px;top:425px;width:413px;height:43px;border:1px solid #cfcfcf;border-radius:22px;background:#fff;font-size:11px;color:#999;padding:14px 0 0 20px}
.search .round-btn{right:8px;top:7px;width:29px;height:29px;background:var(--blue);border:none}

/* section headings */
.h2{position:absolute;left:0;width:1200px;text-align:center;font-size:32px;font-weight:500}
.h2 span{display:inline-block;background:linear-gradient(transparent 72%,var(--blue) 72%,var(--blue) 86%,transparent 86%);padding:0 2px}
.h2.y span{background:linear-gradient(transparent 72%,var(--yellow) 72%,var(--yellow) 86%,transparent 86%)}
.kicker{position:absolute;left:0;width:1200px;text-align:center;font-size:17px;color:var(--muted);font-weight:400}

/* coupon cards */
.coupon{position:absolute;width:298px;height:345px;border-radius:44px;background:var(--blue-soft);box-shadow:5px 5px 0 var(--blue);text-align:center;padding-top:38px}
.coupon.featured{background:var(--yellow-soft);box-shadow:5px 5px 0 var(--yellow)}
.coupon h3{font-size:17px;font-weight:500;line-height:36px;padding:0 20px;text-transform:uppercase}
.coupon h3 em{font-style:normal;color:var(--yellow);font-weight:400}
.coupon.featured h3 em{color:var(--teal)}
.code{display:inline-block;margin-top:10px;border:1.5px dashed var(--yellow);border-radius:6px;padding:8px 16px;font-size:14px;font-weight:400}
.code svg{vertical-align:-3px;margin-left:6px}
.store-mark{display:flex;align-items:center;justify-content:center;gap:8px;height:90px;font-size:20px;font-weight:500;letter-spacing:1px}
.store-mark i{display:block;width:22px;height:22px;border-radius:50%;background:var(--coral)}
.btn{display:inline-block;border:1.5px dashed var(--yellow);border-radius:6px;padding:10px 20px;font-size:14px;font-weight:400;text-transform:uppercase;background:#fff}
.coupon .btn{border-color:var(--blue);background:transparent}
.note{font-size:14px;line-height:34px;text-transform:uppercase;font-weight:400}

/* categories */
.cat{position:absolute;top:1377px;width:183px;height:171px;border-radius:14px;text-align:center;padding-top:28px;font-size:16px;line-height:32px;font-weight:400}
.cat .ic{width:40px;height:40px;margin:0 auto 14px;border-radius:10px}

/* stores */
.store{position:absolute;top:1772px;width:298px;height:345px;border-radius:44px;background:#fff;box-shadow:3px 3px 0 var(--blue);text-align:center;padding-top:40px;overflow:hidden}
.store.featured{box-shadow:3px 4px 0 var(--yellow)}
.store h3{font-size:21px;font-weight:400;display:flex;align-items:center;justify-content:center;gap:10px}
.store h3 i{display:block;width:16px;height:16px;border-radius:50%}
.store p{font-size:16px;line-height:32px;color:var(--muted);margin-top:12px;padding:0 20px}
.store .deal{font-size:17px;line-height:37px;font-weight:500;text-transform:uppercase;margin-top:6px}
.store .deal em{font-style:normal;color:var(--yellow);font-weight:400}
.store.featured .deal em{color:var(--blue-deep)}
.store .btn{margin-top:18px;border:1px solid var(--blue);border-style:solid}
.store .pets{position:absolute;right:0;bottom:0;width:118px;height:100px;border-radius:40px 0 0 0;background:linear-gradient(135deg,#d9b48a,#6b4a33)}

/* about */
.about-copy{left:622px;top:2418px;width:470px;font-size:15px;line-height:35.2px;color:var(--ink)}
.about-copy p+p{margin-top:14px}
.about-copy a{color:var(--blue-deep);text-decoration:none}
.feature{position:absolute;top:2848px;font-size:17px;line-height:35px;font-weight:400;text-transform:uppercase}
.feature .ic{width:48px;height:48px;margin-bottom:38px}

/* footer */
.fhead{position:absolute;top:3108px;font-size:22px;font-weight:500}
.fhead span{background:linear-gradient(transparent 78%,var(--blue) 78%,var(--blue) 90%,transparent 90%)}
.flist{position:absolute;top:3160px;list-style:none;font-size:14px;line-height:37px;font-weight:300}
.contact{position:absolute;left:911px;display:flex;align-items:flex-start;gap:14px;font-size:14px;line-height:24px}
.contact .round-btn{position:static;width:34px;height:34px;flex:none;border-color:#c9e6f3}
.subscribe{left:84px;top:3338px;width:247px;height:42px;border:1px solid #bdbdbd;border-radius:4px;overflow:hidden;display:flex;background:#fff}
.subscribe span{flex:1;font-size:13px;color:#999;padding:14px 0 0 16px}
.subscribe b{width:89px;background:var(--blue-deep);color:#fff;font-weight:400;font-size:16px;text-align:center;padding-top:11px}
.social{position:absolute;top:3440px;width:27px;height:27px;border-radius:50%;border:1.5px solid var(--ink)}
</style>
</head>
<body>

<!-- HERO BAND -->
<div class="band" style="top:0;height:538px"></div>

<header>
  <div class="brand" style="left:112px;top:24px;width:138px;height:138px;font-size:15px">SNOUTSAVER</div>
  <a class="nav active" style="left:532px">Home</a>
  <a class="nav" style="left:605px">Categories
    <svg width="8" height="6" viewBox="0 0 8 6"><path d="M0 0h8L4 5z" fill="#1d1d1f"/></svg></a>
  <a class="nav" style="left:724px">Popular Stores</a>
  <a class="nav" style="left:882px">Latest Deals</a>
  <div class="round-btn" style="left:1055px;top:35px;width:33px;height:33px">
    <svg width="13" height="13" viewBox="0 0 14 14"><circle cx="6" cy="6" r="4.5" fill="none" stroke="#1d1d1f" stroke-width="1.8"/><path d="M9.5 9.5L13 13" stroke="#1d1d1f" stroke-width="1.8"/></svg>
  </div>
</header>

<section class="hero">
  <h1 class="abs hero-title">Save On <em>Everything</em> Your<br>Dog Loves</h1>
  <p class="abs hero-sub">Verified deals updated daily. Your pup deserves the best for less.</p>
  <div class="abs search">SEARCH HERE...
    <div class="round-btn"><svg width="12" height="12" viewBox="0 0 14 14"><circle cx="6" cy="6" r="4.5" fill="none" stroke="#1d1d1f" stroke-width="2"/><path d="M9.5 9.5L13 13" stroke="#1d1d1f" stroke-width="2"/></svg></div>
  </div>
  <div class="ph" role="img" aria-label="Golden retriever sitting in front of a light blue rounded shape"
       style="left:670px;top:100px;width:426px;height:482px;border-radius:48% 48% 50% 50%/40% 40% 60% 60%;background:radial-gradient(circle at 50% 40%,#d9a865 0 30%,var(--blue) 31%)"></div>
</section>

<!-- COUPONS -->
<h2 class="h2" style="top:616px"><span>Our Coupons</span></h2>
<p class="kicker" style="top:694px">VERIFIED DEALS UPDATED DAILY</p>

<article class="coupon" style="left:112px;top:710px">
  <h3><em>20% OFF</em> All Dog Treats</h3>
  <span class="code">CODE: WOOF20</span>
  <div class="store-mark" style="height:110px">HOUNDCARE</div>
  <a class="btn">Get Deal</a>
</article>

<article class="coupon featured" style="left:453px;top:767px">
  <h3><em>$15 OFF</em> Grooming Services</h3>
  <span class="code">CODE: GROOM15<svg width="12" height="14" viewBox="0 0 12 14"><rect x="3" y="0.8" width="8" height="10" rx="1.5" fill="none" stroke="#1d1d1f"/><path d="M1 3.5v9h7" fill="none" stroke="#1d1d1f"/></svg></span>
  <div class="store-mark" style="height:112px"><i></i>PUPSHOP</div>
  <p class="note">Valid for first-time<br>customers only</p>
</article>

<article class="coupon" style="left:796px;top:710px;padding-top:26px">
  <h3><em>Free Shipping</em> On All<br>Travel Gear</h3>
  <span class="code">CODE: TRAVELFREE</span>
  <div class="store-mark" style="height:110px"><i style="background:var(--yellow)"></i>TRAILPUP</div>
  <a class="btn">Get Deal</a>
</article>

<a class="abs btn" style="left:512px;top:1163px">View More Deals</a>

<div class="ph" role="img" aria-label="Pile of dry dog kibble" style="left:0;top:1075px;width:196px;height:258px;background:radial-gradient(ellipse at 40% 85%,#c98a3a 0 35%,transparent 36%),radial-gradient(circle at 60% 30%,#e0a24a 0 10%,transparent 11%)"></div>
<div class="ph" role="img" aria-label="Kitten and spaniel puppy lying together" style="left:913px;top:1120px;width:287px;height:206px;border-radius:60px 0 0 20px;background:linear-gradient(100deg,#cfcac4 0 35%,#d79a55 45%,#b06a2c 100%)"></div>

<!-- CATEGORIES -->
<h2 class="h2 y" style="top:1278px"><span>Our Categories</span></h2>

<a class="cat" style="left:112px;background:#e8f6e6"><div class="ic" style="background:var(--green)"></div>DOG FOOD &amp;<br>TREATS</a>
<a class="cat" style="left:310px;background:#fdf0df"><div class="ic" style="background:#f0a24a;border-radius:50%"></div>TOYS &amp;<br>ACCESSORIES</a>
<a class="cat" style="left:509px;background:#fbe3ea"><div class="ic" style="background:var(--red);border-radius:50% 50% 10px 10px"></div>HEALTH &amp;<br>GROOMING</a>
<a class="cat" style="left:706px;background:#e3f3fb"><div class="ic" style="background:var(--teal);border-radius:50% 10px"></div>TRAINING &amp;<br>SERVICES</a>
<a class="cat" style="left:905px;background:#f0eaf6"><div class="ic" style="background:var(--purple);border-radius:10px 50%"></div>OUTDOOR &amp;<br>TRAVEL</a>

<!-- STORES -->
<div class="band" style="top:1630px;height:643px"></div>
<h2 class="h2" style="top:1677px"><span>Popular Stores</span></h2>

<article class="store" style="left:112px;padding-top:44px">
  <h3><i style="background:var(--pink)"></i>FETCHLY</h3>
  <p>Massive online pet retailer</p>
  <p class="deal">Sitewide <em>96%</em>, Autoship<br>Discounts</p>
  <a class="btn">View Store</a>
  <div class="pets" role="img" aria-label="Cat and boxer dog"></div>
</article>

<article class="store featured" style="left:450px;padding-top:38px">
  <h3><i style="background:#c98a3a"></i>TAILHOUSE</h3>
  <p style="margin-top:6px">National pet chain, products<br>&amp; grooming</p>
  <p class="deal"><em>12$ OFF</em> Grooming,<br><em>67% OFF</em> Treats</p>
  <a class="btn" style="margin-top:10px">View Store</a>
  <div class="pets" role="img" aria-label="Tabby cat and spaniel dog"></div>
</article>

<article class="store" style="left:791px;padding-top:38px">
  <h3><i style="background:var(--yellow)"></i>PAWNEST</h3>
  <p style="margin-top:6px">Retail chain with training &amp;<br>adoption services</p>
  <p class="deal"><em>$18 OFF</em> Orders,<br><em>BOGO</em> Toys</p>
  <a class="btn" style="margin-top:10px">View Store</a>
  <div class="pets" role="img" aria-label="Cat and papillon dog"></div>
</article>

<a class="abs btn" style="left:512px;top:2167px">View All Stores</a>

<!-- ABOUT -->
<div class="ph" role="img" aria-label="Golden retriever sitting in a sunny meadow" style="left:122px;top:2354px;width:412px;height:426px;border-radius:50%;border:6px solid var(--blue-deep);background:radial-gradient(circle at 50% 45%,#c98b45 0 28%,#b7c46a 29%,#6f8f3a 100%)"></div>

<h2 class="abs" style="left:622px;top:2350px;font-size:32px;font-weight:500"><span style="background:linear-gradient(transparent 74%,var(--blue) 74%,var(--blue) 88%,transparent 88%)">About Us</span></h2>
<div class="abs about-copy">
  <p>At SnoutSaver.net, we believe treating your dog should never break the bank. That’s why we sniff out the best pet deals, coupons, and promo codes — so you can give your furry friend more for less.</p>
  <p>Founded by a small team of dog parents, SnoutSaver was built out of frustration: too many fake codes, expired offers, and cluttered coupon sites. We set out to create something better — a place where pet lovers can find <a>real savings, fast.</a></p>
</div>
<a class="abs btn" style="left:622px;top:2741px">Get Started Now</a>

<div class="feature" style="left:111px">
  <svg class="ic" viewBox="0 0 48 48"><circle cx="24" cy="24" r="23" fill="var(--green)"/><path d="M13 25l7 7 15-15" fill="none" stroke="#fff" stroke-width="4" stroke-linecap="round" stroke-linejoin="round"/></svg>
  Deal Verification<br>Badges</div>
<div class="feature" style="left:405px">
  <svg class="ic" viewBox="0 0 48 48"><path d="M24 3l3 6 6 1-4.5 4 1 6L24 17l-5.5 3 1-6L15 10l6-1z" fill="var(--coral)"/><rect x="12" y="26" width="8" height="20" rx="2" fill="var(--yellow)"/><path d="M22 46V28l8-8 3 2-2 8h9a3 3 0 0 1 3 3l-3 13z" fill="var(--coral)"/></svg>
  User Reviews/<br>Ratings</div>
<div class="feature" style="left:668px">
  <svg class="ic" viewBox="0 0 48 48"><rect x="3" y="3" width="28" height="38" rx="3" fill="var(--red)"/><rect x="8" y="9" width="18" height="6" fill="#fff"/><circle cx="34" cy="34" r="12" fill="var(--red)" stroke="#fff" stroke-width="2"/><path d="M34 27v14M31 31h5a2 2 0 0 1 0 4h-4a2 2 0 0 0 0 4h5" fill="none" stroke="#fff" stroke-width="2"/></svg>
  Clear Savings<br>Calculations</div>
<div class="feature" style="left:932px">
  <svg class="ic" viewBox="0 0 48 48"><rect x="5" y="5" width="28" height="38" rx="3" fill="none" stroke="var(--teal)" stroke-width="3"/><path d="M11 16h16M11 23h16M11 30h10" stroke="var(--teal)" stroke-width="3"/><circle cx="34" cy="34" r="8" fill="#fff" stroke="var(--teal)" stroke-width="3"/><path d="M40 40l6 6" stroke="var(--teal)" stroke-width="3"/></svg>
  Expiration Date<br>Transparency</div>

<!-- FOOTER -->
<div class="band" style="top:3055px;height:432px"></div>
<div class="ph" role="img" aria-label="Spaniel dog leaping" style="left:1028px;top:3006px;width:172px;height:146px;border-radius:50% 30% 40% 50%;background:linear-gradient(120deg,#f2e8dc,#b8602a 60%,#7a3d1a)"></div>

<footer>
  <div class="brand" style="left:84px;top:3112px;width:139px;height:139px;font-size:15px">SNOUTSAVER</div>
  <h3 class="fhead" style="left:84px;top:3280px"><span>Subscribe Us</span></h3>
  <div class="abs subscribe"><span>EMAIL ADDRESS</span><b>SUBMIT</b></div>

  <h3 class="fhead" style="left:442px"><span>Quick Links</span></h3>
  <ul class="flist" style="left:442px"><li>Home</li><li>Categories</li><li>Popular Stores</li><li>Latest Deals</li><li>About</li><li>Contact</li></ul>

  <h3 class="fhead" style="left:674px"><span>Categories</span></h3>
  <ul class="flist" style="left:674px"><li>Dog Food &amp; Treats</li><li>Toys &amp; Accessories</li><li>Health &amp; Grooming</li><li>Training &amp; Services</li><li>Outdoor &amp; Travel</li></ul>

  <h3 class="fhead" style="left:911px"><span>Contact Us</span></h3>
  <div class="contact" style="top:3164px"><div class="round-btn"><svg width="12" height="12" viewBox="0 0 12 12"><path d="M2 1l2 0 1 3-1.5 1a7 7 0 0 0 3.5 3.5L8 7l3 1v2a1 1 0 0 1-1 1A9 9 0 0 1 1 2a1 1 0 0 1 1-1z" fill="#1d1d1f"/></svg></div><span style="padding-top:5px">+1 555 014 2287</span></div>
  <div class="contact" style="top:3225px"><div class="round-btn"><svg width="12" height="10" viewBox="0 0 12 10"><rect x="0.5" y="0.5" width="11" height="9" rx="1" fill="#1d1d1f"/><path d="M1 1l5 4 5-4" fill="none" stroke="#fff"/></svg></div><span style="padding-top:5px">hello@snoutsaver.net</span></div>
  <div class="contact" style="top:3286px"><div class="round-btn"><svg width="10" height="13" viewBox="0 0 10 13"><path d="M5 0a5 5 0 0 1 5 5c0 3-5 8-5 8S0 8 0 5a5 5 0 0 1 5-5z" fill="#1d1d1f"/><circle cx="5" cy="5" r="1.8" fill="#fff"/></svg></div><span>48 Fetch Street<br>Dayton, OH 45402</span></div>

  <div class="abs" style="left:76px;top:3419px;width:1046px;height:1px;background:var(--line)"></div>
  <p class="abs" style="left:76px;top:3447px;font-size:12px;font-weight:400">©2025 COPYRIGHTS <span style="color:var(--blue-deep)">SNOUTSAVER</span>. ALL RIGHTS RESERVED</p>
  <span class="social" style="left:998px" aria-label="Social link"></span>
  <span class="social" style="left:1030px" aria-label="Social link"></span>
  <span class="social" style="left:1062px" aria-label="Social link"></span>
  <span class="social" style="left:1094px" aria-label="Social link"></span>
</footer>

</body>
</html>
```